General Surgeon flyer to be distributed to GPs

I am a general surgeon and I would like to have a flyer designed aiming to introduce myself to GPs.

Name: Dr Tobias Lindqvar MD, FRACS
Address: Suite 4C, Brellam private hospital, 418 Corvell Parade, Harlow Vale, VIC, 3179
T: (03) 9587 6102
F: (03) 9463 1178
E: referrals@quillfordsurgeons.com.au
Website: www.quillfordsurgeons.com.au

Tobias is a highly trained general surgeon, having completed extensive surgical training at Tarrowby health, Pellington and Corrigan Health networks. He further specialized by completing a fellowship in Oesophagogastric and Bariatric Surgery at St Aldric’s Hospital Melbourne, one of Victoria’s leading Upper GI surgical centres.

With expertise in both advanced laparoscopic and open surgical techniques, he performs a wide range of procedures involving the gastrointestinal system, abdominal wall hernias, as well as other major and minor general surgical operations. In addition to holding appointments at Tarrowby Health, he also operates at Brellam and Fernwick Private Hospitals.

Dr Lindqvar is committed to providing patient-centred care with a focus on surgical precision, safety, and long-term health outcomes.

He is also fluent in Farsi/Pesrian.
Outside of surgery, Tobias enjoys playings classical piano and spending time with his 6-year-old Bordoodle on long walks.

Upper GI & Bariatric Surgery:
Hiatus hernia repair, sleeve gastrectomy, gastric bypass
General Surgery conditions:
Gallbladder Surgery: Laparoscopic cholecystectomy
Hernia Repair: Laparoscopic and open surgery (inguinal,
umbilical, incisional)
Anorectal Procedures: Haemorrhoidectomy, haemorrhoid banding
Hand Surgery: Carpal tunnel release, Lymph Node Biopsy
Ingrown Toenail Surgery
Skin & Soft Tissue Surgery: Skin cancer removal, lipoma and
sebaceous cyst excision
Emergency Surgery: Laparotomy, Appendicectomy, bowel resection
Endoscopy: Diagnostic and therapeutic procedures

```html
<!DOCTYPE html>
<html lang="en">
<head>
<meta charset="utf-8">
<title>Dr Tobias Lindqvar – General Surgeon</title>
<link href="https://fonts.googleapis.com/css2?family=Montserrat:wght@400;500;700;800&display=swap" rel="stylesheet">
<style>
  :root {
    --navy-deep: #0f3159;
    --navy: #174578;
    --name-blue: #5b86bf;
    --ice: #deedfc;
    --grey-band: #e4e5e7;
    --grey-strip: #d6d7d9;
    --address-blue: #2b5a8f;
    --ink: #0f3159;
    --white: #ffffff;
    --badge-grey: #c9d3df;
    --practice-cyan: #12c4ef;
  }
  * { margin: 0; padding: 0; box-sizing: border-box; }
  html, body { width: 848px; height: 1200px; overflow: hidden; background: var(--white); }
  body { font-family: "Montserrat", sans-serif; color: var(--ink); }
  .flyer { position: relative; width: 848px; height: 1200px; }

  .site-url {
    position: absolute; top: 76px; left: 0; width: 848px; text-align: center;
    font-size: 20px; letter-spacing: 4.1px; color: var(--ink); font-weight: 400;
  }

  .name-band {
    position: absolute; top: 121px; left: 0; width: 848px; height: 61px;
    background: var(--navy-deep); display: flex; align-items: center; justify-content: center;
    color: var(--name-blue); font-size: 24px; padding-left: 2px;
  }
  .name-band .name { font-weight: 800; letter-spacing: 0.2px; }
  .name-band .credentials { font-weight: 500; margin-left: 15px; }

  .bio-band {
    position: absolute; top: 182px; left: 0; width: 848px; height: 299px;
    background: var(--navy); color: var(--white); padding: 27px 64px 0 68px;
  }
  .bio-band p { font-size: 16.2px; line-height: 23px; margin-bottom: 18px; }
  .bio-band p.justified { text-align: justify; letter-spacing: 0.3px; }
  .bio-band p.spaced { letter-spacing: 0.7px; }
  .bio-band p.plain { letter-spacing: 0.15px; }

  .services-band {
    position: absolute; top: 481px; left: 0; width: 848px; height: 465px;
    background: var(--ice); padding: 32px 0 0 70px;
  }
  .services { list-style: none; }
  .service { position: relative; padding-left: 21px; margin-bottom: 11px; }
  .service::before {
    content: ""; position: absolute; left: 0; top: 6px; width: 9px; height: 9px;
    border-radius: 50%; background: var(--ink);
  }
  .service-title { font-size: 16.6px; font-weight: 700; letter-spacing: 0.4px; line-height: 20px; }
  .service-detail { font-size: 16.4px; font-weight: 400; letter-spacing: 0.4px; line-height: 23px; }

  .credentials-band {
    position: absolute; top: 946px; left: 0; width: 848px; height: 107px; background: var(--grey-band);
  }
  .college-badge {
    position: absolute; left: 208px; top: 30px; width: 292px; height: 48px;
    border-radius: 6px; background: var(--badge-grey);
  }
  .practice-mark { position: absolute; left: 560px; top: 13px; display: flex; align-items: center; gap: 10px; }
  .practice-mark .dot { width: 80px; height: 80px; border-radius: 50%; background: var(--practice-cyan); }
  .practice-mark .practice-name { font-size: 15px; font-weight: 700; color: var(--ink); line-height: 18px; }

  .address-strip {
    position: absolute; top: 1053px; left: 0; width: 848px; height: 31px; background: var(--grey-strip);
    display: flex; align-items: center; justify-content: center;
    font-size: 12.6px; color: var(--address-blue); letter-spacing: 0.4px;
  }

  .contact-lines {
    position: absolute; top: 1119px; left: 69px; font-size: 10.4px; letter-spacing: 1.6px;
    line-height: 13.5px; color: var(--ink);
  }
  .phone { position: absolute; top: 1110px; left: 498px; display: flex; align-items: center; }
  .phone svg { width: 20px; height: 33px; }
  .phone-number { margin-left: 20px; font-size: 32.5px; font-weight: 700; letter-spacing: 0.5px; color: var(--ink); }
</style>
</head>
<body>
<div class="flyer">
  <div class="site-url">www.quillfordsurgeons.com.au</div>

  <header class="name-band">
    <span class="name">DR TOBIAS LINDQVAR</span><span class="credentials">MD, FRACS</span>
  </header>

  <section class="bio-band">
    <p class="justified">With expertise in both advanced laparoscopic and open surgical techniques, he performs a wide range of procedures involving the gastrointestinal system, abdominal wall hernias, as well as other major and minor general surgical operations. In addition to holding appointments at Tarrowby Health, he also operates at Brellam and Fernwick Private Hospitals.</p>
    <p class="spaced">Dr Lindqvar is committed to providing patient-centred care with a focus on surgical precision, safety, and long-term health outcomes.</p>
    <p class="plain">He is also fluent in Farsi/Pesrian. Outside of surgery, Tobias enjoys playings classical piano and spending time with his 6-year-old Bordoodle on long walks.</p>
  </section>

  <section class="services-band">
    <ul class="services">
      <li class="service"><div class="service-title">UPPER GI &amp; BARIATRIC SURGERY</div><div class="service-detail">Upper GI &amp; Bariatric Surgery:</div></li>
      <li class="service"><div class="service-title">GENERAL SURGERY CONDITIONS</div><div class="service-detail">Gallbladder Surgery: Laparoscopic cholecystectomy</div></li>
      <li class="service"><div class="service-title">HERNIA REPAIR</div><div class="service-detail">Laparoscopic and open surgery (inguinal, umbilical, incisional)</div></li>
      <li class="service"><div class="service-title">ANORECTAL PROCEDURES</div><div class="service-detail">Haemorrhoidectomy, haemorrhoid banding</div></li>
      <li class="service"><div class="service-title">HAND SURGERY</div><div class="service-detail">Carpal tunnel release, Lymph Node Biopsy Ingrown Toenail Surgery</div></li>
      <li class="service"><div class="service-title">SKIN &amp; SOFT TISSUE SURGERY</div><div class="service-detail">Skin cancer removal, lipoma and sebaceous cyst excision</div></li>
      <li class="service"><div class="service-title">EMERGENCY SURGERY</div><div class="service-detail">Laparotomy, Appendicectomy, bowel resection Endoscopy: Diagnostic and<br>therapeutic procedures</div></li>
    </ul>
  </section>

  <section class="credentials-band">
    <div class="college-badge" role="img" aria-label="Surgical college fellowship badge"></div>
    <div class="practice-mark">
      <span class="dot"></span>
      <span class="practice-name">Quillford<br>Surgeons</span>
    </div>
  </section>

  <div class="address-strip">Suite 4C, Brellam private hospital, 418 Corvell Parade, Harlow Vale, VIC, 3179</div>

  <footer>
    <div class="contact-lines">
      <div>www.quillfordsurgeons.com.au</div>
      <div>referrals@quillfordsurgeons.com.au</div>
    </div>
    <div class="phone">
      <svg viewBox="0 0 20 33" aria-hidden="true">
        <rect x="1.5" y="1.5" width="17" height="30" rx="3" fill="none" stroke="#0f3159" stroke-width="2.6"/>
        <line x1="7" y1="27" x2="13" y2="27" stroke="#0f3159" stroke-width="2"/>
      </svg>
      <span class="phone-number">(03) 9587 6102</span>
    </div>
  </footer>
</div>
</body>
</html>
```